LDI Illustration Web Design

Create illustration web design company for Lumaviro Darsa Informatika (LDI). I more prefer design with illustration concept. Detail for requirement please see attach file. I'm also attach LDI logo. This logo had 2 type, 2D design and 3D design. You can chose one of them, or used both.
For the winner or had good design would be possible to private project to completeness this website
Attach file requirement is guidance for design, but any changes are welcome
Updates
Sorry, I forgot about contact. Please add menu contact. You can put this menu besides login menu or part of menu level #1, or put on some where to adjust your design. Menu contact will give pop up window to email LDI Company and Company Information (Address, Telephone, etc)
Target Market(s)
Company (Business To Business)
Industry/Entity Type
It Company
Look and feel
Each slider illustrates characteristics of the customer's brand and the style your logo design should communicate.

```html
<!DOCTYPE html>
<html lang="en">
<head>
<meta charset="utf-8">
<title>LDI — Welcome aboard</title>
<link rel="stylesheet" href="https://fonts.googleapis.com/css2?family=Michroma&family=Cousine&family=Arimo&display=swap">
<style>
  :root {
    --space-deep: #0a0a3a;
    --space-mid: #2b2280;
    --space-edge: #08082a;
    --lime: #a8d21a;
    --lime-dark: #3f8a14;
    --green-top: #7cc63a;
    --green-bottom: #1c6a1c;
    --blue-top: #3ab4e8;
    --blue-bottom: #1738c8;
    --cyan-glow: #20f0ff;
    --field: #0f4e86;
    --field-text: #5fb4de;
    --welcome: #5fc4ee;
    --label: #f2fbff;
    --dot: #d8ff3a;
  }
  * { margin: 0; padding: 0; box-sizing: border-box; }
  html, body { width: 1200px; height: 800px; overflow: hidden; background: var(--space-edge); }
  .page {
    position: relative; width: 1200px; height: 800px; overflow: hidden;
    background: radial-gradient(ellipse 70% 60% at 50% 45%, var(--space-mid) 0%, #1d1766 45%, var(--space-deep) 80%, var(--space-edge) 100%);
  }
  .stage { position: absolute; inset: 0; }
  .brand {
    position: absolute; left: 226px; top: 16px; height: 52px;
    display: flex; align-items: center; gap: 10px;
    font-family: "Michroma", sans-serif; font-size: 40px; color: var(--lime); text-decoration: none;
  }
  .brand-dot { width: 48px; height: 48px; border-radius: 50%; background: var(--lime); }
  .welcome {
    position: absolute; left: 441px; top: 39px;
    font-family: "Cousine", monospace; font-size: 14px; color: var(--welcome); letter-spacing: 0.5px;
  }
  .login-bar { position: absolute; left: 728px; top: 17px; display: flex; align-items: center; gap: 5px; }
  .login-field {
    width: 109px; height: 15px; border-radius: 8px; border: 0; background: var(--field);
    font-family: "Arimo", sans-serif; font-size: 9px; color: var(--field-text); padding-left: 18px;
  }
  .login-field::placeholder { color: var(--field-text); }
  .login-go {
    width: 21px; height: 21px; border-radius: 50%; border: 0; background: var(--lime);
    font-family: "Arimo", sans-serif; font-size: 9px; color: #fff; margin-left: 4px;
  }
  .node-label { font-family: "Michroma", sans-serif; font-size: 12px; fill: var(--label); letter-spacing: 1px; }
</style>
</head>
<body>
<main class="page">
  <svg class="stage" width="1200" height="800" viewBox="0 0 1200 800">
    <defs>
      <radialGradient id="core-fill" cx="50%" cy="50%" r="55%">
        <stop offset="0%" stop-color="#e8ffff"/>
        <stop offset="40%" stop-color="var(--cyan-glow)"/>
        <stop offset="75%" stop-color="#7ecb2a"/>
        <stop offset="100%" stop-color="#1a88cc"/>
      </radialGradient>
      <linearGradient id="beam" x1="0" y1="0" x2="0" y2="1">
        <stop offset="0%" stop-color="#20e8ff" stop-opacity="0.85"/>
        <stop offset="100%" stop-color="#20e8ff" stop-opacity="0"/>
      </linearGradient>
      <radialGradient id="pod-green" cx="50%" cy="25%" r="80%">
        <stop offset="0%" stop-color="var(--green-top)"/>
        <stop offset="100%" stop-color="var(--green-bottom)"/>
      </radialGradient>
      <radialGradient id="pod-blue" cx="50%" cy="25%" r="80%">
        <stop offset="0%" stop-color="var(--blue-top)"/>
        <stop offset="100%" stop-color="var(--blue-bottom)"/>
      </radialGradient>
      <radialGradient id="planet" cx="50%" cy="40%" r="60%">
        <stop offset="0%" stop-color="#a5a030"/>
        <stop offset="100%" stop-color="#5a4a20"/>
      </radialGradient>
    </defs>

    <circle cx="906" cy="-28" r="68" fill="url(#planet)" role="img" aria-label="Distant planet"/>
    <circle cx="241" cy="568" r="11" fill="#9a2ad0" role="img" aria-label="Small purple planet"/>

    <path d="M540 520 L700 520 L640 740 L620 740 Z" fill="url(#beam)" opacity="0.6"/>

    <g class="connectors" stroke-width="5" stroke-linecap="round">
      <line x1="598" y1="205" x2="604" y2="240" stroke="#3a8ad0"/>
      <line x1="350" y1="252" x2="420" y2="306" stroke="#2f6a5a"/>
      <line x1="340" y1="390" x2="390" y2="414" stroke="#2a6ab0"/>
      <line x1="410" y1="535" x2="450" y2="500" stroke="#2f7a3a"/>
      <line x1="870" y1="290" x2="830" y2="322" stroke="#2f6a5a"/>
      <line x1="830" y1="520" x2="800" y2="488" stroke="#2a8ab8"/>
    </g>

    <ellipse cx="622" cy="392" rx="240" ry="160" fill="url(#core-fill)" role="img" aria-label="Central glowing company emblem"/>

    <g class="nav-nodes">
      <a href="#company">
        <ellipse cx="598" cy="182" rx="74" ry="35" fill="url(#pod-blue)"/>
        <text class="node-label" x="602" y="181" text-anchor="middle">COMPANY</text>
        <g fill="var(--dot)"><circle cx="545" cy="204" r="1.5"/><circle cx="551" cy="206" r="1.5"/><circle cx="557" cy="208" r="1.5"/><circle cx="563" cy="209" r="1.5"/></g>
      </a>
      <a href="#services">
        <ellipse cx="314" cy="230" rx="74" ry="35" fill="url(#pod-green)"/>
        <text class="node-label" x="315" y="227" text-anchor="middle">SERVICES</text>
        <g fill="var(--dot)"><circle cx="266" cy="253" r="1.5"/><circle cx="272" cy="255" r="1.5"/><circle cx="278" cy="257" r="1.5"/><circle cx="285" cy="258" r="1.5"/></g>
      </a>
      <a href="#blog">
        <ellipse cx="910" cy="266" rx="74" ry="35" fill="url(#pod-green)"/>
        <text class="node-label" x="910" y="266" text-anchor="middle">BLOG</text>
        <g fill="var(--dot)"><circle cx="876" cy="294" r="1.5"/><circle cx="882" cy="296" r="1.5"/><circle cx="888" cy="297" r="1.5"/><circle cx="895" cy="298" r="1.5"/></g>
      </a>
      <a href="#products">
        <ellipse cx="302" cy="367" rx="74" ry="35" fill="url(#pod-blue)"/>
        <text class="node-label" x="304" y="367" text-anchor="middle">PRODUCTS</text>
        <g fill="var(--dot)"><circle cx="251" cy="390" r="1.5"/><circle cx="257" cy="392" r="1.5"/><circle cx="263" cy="393" r="1.5"/><circle cx="270" cy="394" r="1.5"/></g>
      </a>
      <a href="#contact">
        <ellipse cx="380" cy="562" rx="74" ry="35" fill="url(#pod-green)"/>
        <text class="node-label" x="382" y="560" text-anchor="middle">CONTACT US</text>
        <g fill="var(--dot)"><circle cx="337" cy="585" r="1.5"/><circle cx="343" cy="588" r="1.5"/><circle cx="349" cy="589" r="1.5"/><circle cx="356" cy="590" r="1.5"/></g>
      </a>
      <a href="#clients">
        <ellipse cx="874" cy="541" rx="74" ry="35" fill="url(#pod-blue)"/>
        <text class="node-label" x="876" y="540" text-anchor="middle">CLIENTS</text>
        <g fill="var(--dot)"><circle cx="833" cy="567" r="1.5"/><circle cx="839" cy="569" r="1.5"/><circle cx="845" cy="570" r="1.5"/><circle cx="852" cy="570" r="1.5"/></g>
      </a>
    </g>
  </svg>

  <a class="brand" href="#home" aria-label="Lumaviro Darsa Informatika"><span class="brand-dot"></span>LDI</a>
  <p class="welcome">Welcome aboard ...</p>

  <form class="login-bar">
    <input class="login-field" type="text" placeholder="Login" aria-label="Login">
    <input class="login-field" type="password" placeholder="Password" aria-label="Password">
    <button class="login-go" type="button">Go</button>
  </form>
</main>
</body>
</html>
```